Storm Restoration Contractor needs a professional letterhead design

Looking for a professional letterhead design. Not looking for your cheapo MS Word standard ones that are readily available. Dont want it to be cookie cutter look like ones readily available online. We just recently changed our logo and want to freshen up all our documents. Our company handles restoring a property back to a pre-loss condition after a storm damages it. For example, wind, hail, flood, fire losses.

Target Market(s)

Property Owners, Homeowners, Property Owners, Commercial Property Owners, Property Management Companies

Industry/Entity Type

Construction Company

Requirements
Must have
• Professional, Use 1 of 2 logo options
• Storm Restoration, Roofing, Siding, Windows

```html
<!DOCTYPE html>
<html lang="en">
<head>
<meta charset="utf-8">
<title>Harborline Exteriors Letterhead</title>
<link rel="stylesheet" href="https://fonts.googleapis.com/css2?family=Open+Sans:wght@400;600;700&display=swap">
<style>
  :root {
    --backdrop: #c9c9c9;
    --paper: #ffffff;
    --brand-blue: #1f74c1;
    --brand-grey: #4a4a4c;
    --ink: #3a3a3a;
    --ink-soft: #5a5a5a;
    --signature-tone: #d9dde3;
  }
  * { margin: 0; padding: 0; box-sizing: border-box; }
  html, body {
    width: 1200px; height: 795px; overflow: hidden;
    background: var(--backdrop);
    font-family: "Open Sans", Arial, sans-serif;
  }
  .canvas {
    position: relative; width: 1200px; height: 795px;
    display: flex; align-items: center; justify-content: center;
  }
  .letterhead {
    position: relative; width: 520px; height: 736px;
    background: var(--paper); overflow: hidden;
    box-shadow: 0 2px 8px rgba(0,0,0,0.18);
  }
  .brand {
    position: absolute; top: 44px; left: 40px;
    display: flex; align-items: center; gap: 8px;
  }
  .brand-mark {
    width: 34px; height: 34px; border-radius: 50%;
    background: var(--brand-blue);
  }
  .brand-name {
    font-size: 13px; font-weight: 600; color: var(--brand-blue);
    letter-spacing: 0.06em; text-transform: uppercase;
  }
  .contact {
    position: absolute; top: 40px; right: 36px;
    text-align: right; font-size: 6.5px; line-height: 9px; color: var(--ink-soft);
  }
  .contact-icons { display: flex; justify-content: flex-end; gap: 2px; margin-bottom: 2px; }
  .contact-icons span {
    width: 6px; height: 6px; border-radius: 50%; background: var(--brand-blue);
  }
  .letter {
    position: absolute; top: 190px; left: 40px; width: 440px;
    font-size: 7.6px; line-height: 10.4px; color: var(--ink-soft);
  }
  .salutation {
    font-size: 10px; font-weight: 700; color: var(--ink); margin-bottom: 8px;
  }
  .letter p { margin-bottom: 10px; }
  .signature {
    position: absolute; top: 430px; left: 44px;
    width: 90px; height: 34px; border-radius: 4px;
    background: var(--signature-tone);
  }
  .footer {
    position: absolute; left: 0; bottom: 0; width: 520px; height: 280px;
  }
  .footer svg { display: block; width: 100%; height: 100%; }
  .services {
    position: absolute; left: 22px; bottom: 22px;
    font-size: 10px; color: var(--paper); letter-spacing: 0.02em;
  }
</style>
</head>
<body>
<div class="canvas">
  <main class="letterhead">
    <header>
      <div class="brand">
        <span class="brand-mark"></span>
        <span class="brand-name">Harborline Exteriors</span>
      </div>
      <div class="contact">
        <div class="contact-icons"><span></span><span></span><span></span><span></span></div>
        <div>555-014-2866</div>
        <div>555-014-1566</div>
        <div>info@harborlineexteriors.com</div>
        <div>www.harborlineexteriors.com</div>
      </div>
    </header>

    <section class="letter">
      <div class="salutation">Dear Mr. John,</div>
      <p>Lorem Ipsum is simply dummy text of the printing and typesetting industry. Lorem Ipsum has been the industry's standard dummy text ever since the 1500s, when an unknown printer took a galley of type and scrambled it to make a type specimen book. It has survived not only five centuries, but also the leap into electronic typesetting, remaining essentially unchanged.</p>
      <p>The standard chunk of Lorem Ipsum used since the 1500s is reproduced below for those interested. Sections 1.10.32 and 1.10.33 from "de Finibus Bonorum et Malorum" by Cicero are also reproduced in their exact original form, accompanied by English versions from the 1914 translation by H. Rackham.</p>
      <p>Lorem Ipsum is simply dummy text of the printing and typesetting industry. Lorem Ipsum has been the industry's standard dummy text ever since the 1500s, when an unknown printer took a galley of type and scrambled it to make a type specimen book. It has survived not only five centuries, but also the leap into electronic typesetting, remaining essentially unchanged. It was popularised in the</p>
    </section>

    <div class="signature" role="img" aria-label="Handwritten signature of the sender"></div>

    <footer class="footer">
      <svg viewBox="0 0 520 280" preserveAspectRatio="none" aria-hidden="true">
        <path d="M0 170 C 160 200, 330 150, 420 90 C 460 62, 495 40, 520 28 L520 50 C 480 70, 450 95, 420 115 C 330 175, 170 215, 0 200 Z" fill="var(--brand-grey)"/>
        <path d="M0 215 C 170 225, 330 190, 430 120 C 470 92, 500 72, 520 62 L520 280 L0 280 Z" fill="var(--brand-blue)"/>
      </svg>
      <div class="services">Storm Restoration | Roofing | Siding | Windows</div>
    </footer>
  </main>
</div>
</body>
</html>
```